BUSINESS CARD DESIGN

NAME- DALE VORSKIN
PHONE NUMER - 555- 714-9082
EMAIL- OFFICE@TRV-GROUNDMAKRZ.COM
BACK OF CARD- SPEACIALIZES IN LAND CLEARING, FORESTRY MUCLHING AND EXCAVATION

Contact Information for Business Card

NAME- DALE VORSKIN PHONE NUMER - 555- 714-9082 EMAIL- OFFICE@TRV-GROUNDMAKRZ.COM BACK OF CARD- SPEACIALIZES IN LAND CLEARING , MUCLHING AND EXCAVATION

```html
<!DOCTYPE html>
<html lang="en">
<head>
<meta charset="utf-8">
<title>Traverse Groundmakrz – Business Card</title>
<link rel="stylesheet" href="https://fonts.googleapis.com/css2?family=Orbitron:wght@700;800&display=swap">
<style>
  :root{
    --canvas:#ffffff;
    --card:#000000;
    --green:#22ff14;
    --silver:#cfcfcf;
    --silver-dark:#9a9a9a;
  }
  *{margin:0;padding:0;box-sizing:border-box}
  html,body{width:1200px;height:1132px;overflow:hidden;background:var(--canvas)}
  body{position:relative;font-family:"Orbitron",sans-serif}

  .card{position:absolute;left:248px;width:688px;height:394px;background:var(--card);overflow:hidden}
  .card--front{top:106px}
  .card--back{top:592px}

  .card__wave{position:absolute;left:0;top:0;width:100%;height:100%}

  .brand{position:absolute;display:flex;flex-direction:column;align-items:center;color:var(--green);font-weight:800;text-align:center}
  .brand__circle{border:4px solid var(--green);border-radius:50%}
  .brand__name{line-height:1.1;letter-spacing:.02em}
  .brand__sub{letter-spacing:.35em}
  .brand__phone{letter-spacing:.9em;margin-right:-.9em}

  .card--front .brand{left:66px;top:100px;width:200px}
  .card--front .brand__circle{width:104px;height:104px;margin-bottom:14px}
  .card--front .brand__name{font-size:16px}
  .card--front .brand__sub{font-size:9px;margin-top:3px}
  .card--front .brand__phone{font-size:8px;margin-top:6px}

  .card--back .brand{left:224px;top:64px;width:250px}
  .card--back .brand__circle{width:136px;height:136px;margin-bottom:18px}
  .card--back .brand__name{font-size:19px}
  .card--back .brand__sub{font-size:11px;margin-top:3px}
  .card--back .brand__phone{font-size:9px;margin-top:8px}

  .identity{position:absolute;left:342px;top:83px;height:75px;border-left:3px solid var(--green);padding-left:13px}
  .identity__name,.identity__role{
    font-weight:800;font-size:22px;letter-spacing:.03em;line-height:1;
    background:linear-gradient(180deg,#f2f2f2 0%,var(--silver) 50%,var(--silver-dark) 100%);
    -webkit-background-clip:text;background-clip:text;color:transparent
  }
  .identity__name{margin-top:10px}
  .identity__role{margin-top:15px}

  .contacts{position:absolute;left:352px;top:234px;list-style:none}
  .contacts__item{display:flex;align-items:center;height:18px;margin-bottom:17px;color:#e8e8e8;font-weight:700;font-size:11px;letter-spacing:.06em}
  .contacts__item:nth-child(2){margin-bottom:14px}
  .contacts__icon{width:20px;height:18px;margin-right:10px;flex:none}

  .tagline{position:absolute;left:0;width:100%;top:294px;color:var(--green);font-weight:800;font-size:11.5px;line-height:1.12;text-align:center;letter-spacing:.02em}
</style>
</head>
<body>

<section class="card card--front" aria-label="Business card front">
  <svg class="card__wave" viewBox="0 0 860 492" preserveAspectRatio="none" aria-hidden="true">
    <path fill="var(--green)" d="M0 402 C40 412 80 450 120 452 C170 454 200 428 250 429 C320 430 400 482 480 482 C540 482 570 417 620 417 C680 417 730 467 790 467 C820 467 840 460 860 457 L860 492 L0 492 Z"/>
  </svg>

  <div class="brand">
    <div class="brand__circle"></div>
    <div class="brand__name">TRAVERSE</div>
    <div class="brand__sub">GROUNDMAKRZ LLC</div>
    <div class="brand__phone">555-714-9082</div>
  </div>

  <div class="identity">
    <p class="identity__name">DALE VORSKIN</p>
    <p class="identity__role">OWNER</p>
  </div>

  <ul class="contacts">
    <li class="contacts__item">
      <svg class="contacts__icon" viewBox="0 0 20 18" aria-hidden="true"><path fill="none" stroke="var(--green)" stroke-width="1.4" d="M4 2 L7 2 L8.5 6 L6.5 7.5 C7.5 10 9.5 12 12 13 L13.5 11 L17.5 12.5 L17.5 15.5 C10 16.5 3 10 4 2 Z"/><path fill="none" stroke="var(--green)" stroke-width="1.2" d="M12 2 A5 5 0 0 1 17 7 M12 4.5 A2.5 2.5 0 0 1 14.5 7"/></svg>
      +555- 714-9082
    </li>
    <li class="contacts__item">
      <svg class="contacts__icon" viewBox="0 0 20 18" aria-hidden="true"><rect x="1" y="3" width="18" height="12" fill="none" stroke="var(--green)" stroke-width="1.4"/><circle cx="6" cy="8" r="1.8" fill="var(--green)"/><path fill="var(--green)" d="M3 13 C3 10 9 10 9 13 Z"/><path stroke="var(--green)" stroke-width="1.3" d="M11 7 H17 M11 9.5 H17 M11 12 H15"/></svg>
      OFFICE@TRV-GROUNDMAKRZ.COM
    </li>
    <li class="contacts__item">
      <svg class="contacts__icon" viewBox="0 0 20 18" aria-hidden="true"><g fill="none" stroke="var(--green)" stroke-width="1.3"><circle cx="10" cy="9" r="7.5"/><ellipse cx="10" cy="9" rx="3.2" ry="7.5"/><path d="M2.5 9 H17.5 M4 5 H16 M4 13 H16"/></g></svg>
      &nbsp;WWW.GROUNDMAKRZ.COM
    </li>
  </ul>
</section>

<section class="card card--back" aria-label="Business card back">
  <svg class="card__wave" viewBox="0 0 860 492" preserveAspectRatio="none" aria-hidden="true">
    <path fill="var(--green)" d="M0 402 C40 412 80 450 120 452 C170 454 200 428 250 429 C320 430 400 482 480 482 C540 482 570 417 620 417 C680 417 730 467 790 467 C820 467 840 460 860 457 L860 492 L0 492 Z"/>
  </svg>

  <div class="brand">
    <div class="brand__circle"></div>
    <div class="brand__name">TRAVERSE</div>
    <div class="brand__sub">GROUNDMAKRZ LLC</div>
    <div class="brand__phone">555-714-9082</div>
  </div>

  <p class="tagline">SPEACIALIZES IN LAND CLEARING<br>MUCLHING AND EXCAVATION</p>
</section>

</body>
</html>
```